Christian Media Company Website

I am looking to design an easy to follow, sleek, creative website for my Christian video Bible study platform. On this platform you will be able to sign up to have access to dozens of free high-quality video Bible studies. With that being said There will be a total of 3 pages needed.

First, I will need the home page. This should contain all critical information to inform the customer. The design should be easy to follow, professional, and creative. I will post to some websites I like, if you just copy the website in your design will be removed immediately.

Secondly, we will need a landing Bible study page for people to look through the Bible studies to select one. I have uploaded Study images below with the aspect ratio I want for the design (for each Bible study image). There should be 2 sections Topical studies and Doctrinal Studies (with series under each section). I would like for people to be able to slide left or right through the studies under each category.

Lastly, we will need a video series page. This page needs to have the video they are watching, a playlist of the other videos, as well as a place to put the speaker's image and description. We will have studies that they can download so please make a place for this.

I will upload our color in the files along with our logo! Looking forward to seeing what you all will come up with!

Websites I like :
https://lanternvale.org/
https://www.quillharborfilms.org/
https://www.dunmorel.com/
https://tessavint.org/

Target Market(s)

Christians

Industry/Entity Type

Christian Video Design

Coding

Coded - Design and coding required

Number of Pages Required

3 page

Font styles to use
Sans Serif

Colors
00AB8E
00BBA5
67D7C9
C6EFE9
E9F9F6

Requirements
Should not have
• Pre-Used Templates

```html
<!DOCTYPE html>
<html lang="en">
<head>
<meta charset="utf-8">
<title>Kindred Path — Video Bible Studies</title>
<link href="https://fonts.googleapis.com/css2?family=Roboto:wght@400;500;700;900&family=Montserrat:wght@400;600;700;800&display=swap" rel="stylesheet">
<style>
:root{
  --teal:#00bba5;
  --teal-dark:#00ab8e;
  --teal-mid:#67d7c9;
  --teal-pale:#c6efe9;
  --teal-wash:#e9f9f6;
  --ink:#1d1d1f;
  --body:#777;
  --footer:#232323;
  --white:#fff;
}
*{box-sizing:border-box;margin:0;padding:0}
html,body{width:1200px;height:3991px;overflow:hidden}
body{position:relative;font-family:"Roboto",Arial,sans-serif;color:var(--ink);background:var(--white)}
a{color:inherit;text-decoration:none}

/* header */
.site-header{position:absolute;left:0;top:0;width:1200px;height:94px;background:var(--white)}
.brand{position:absolute;left:110px;top:22px;display:flex;align-items:center;gap:12px}
.brand-mark{width:42px;height:42px;border:4px solid var(--teal)}
.brand-name{font-family:"Montserrat",sans-serif;font-weight:700;font-size:22px;line-height:26px;color:var(--teal);width:130px}
.main-nav{position:absolute;top:38px;left:577px;display:flex;gap:34px;font-size:14px;font-weight:700;text-transform:uppercase}
.main-nav .active{color:var(--teal)}
.btn-access{position:absolute;left:930px;top:26px;width:158px;height:42px;border-radius:21px;background:var(--teal);color:#fff;font-size:14px;font-weight:700;display:flex;align-items:center;justify-content:center}

/* hero */
.hero{position:absolute;left:0;top:94px;width:1200px;height:589px;background:linear-gradient(100deg,#5f6a55 0%,#7d8b72 35%,#8c96a3 60%,#6b7658 100%)}
.hero-title{position:absolute;left:111px;top:186px;font-family:"Montserrat",sans-serif;font-weight:800;font-size:43px;color:#fff;letter-spacing:-1px}
.hero-text{position:absolute;left:111px;top:254px;width:440px;font-size:16px;line-height:27px;color:#fff}
.btn-pill{display:flex;align-items:center;justify-content:center;gap:8px;border-radius:26px;font-weight:700;font-size:15px;text-transform:uppercase}
.hero .btn-pill{position:absolute;left:112px;top:336px;width:196px;height:48px;background:var(--teal);color:#fff}
.dots{position:absolute;left:580px;top:532px;display:flex;gap:4px}
.dots span{width:10px;height:10px;border:2px solid #fff;border-radius:50%}
.dots span:first-child{background:#fff}

/* series tiles */
.tile{position:absolute;top:700px;width:281px;height:391px;display:flex;flex-direction:column;align-items:center;justify-content:flex-end;padding-bottom:16px;color:#fff;font-size:14px}
.tile-title{font-family:"Montserrat",sans-serif;font-weight:800;font-size:38px;line-height:1.05;text-align:center;margin-bottom:10px}
.t1{left:15px;background:linear-gradient(180deg,#9aa58c,#4a4f40)}
.t2{left:311px;background:var(--teal-mid);justify-content:center}
.t2 .tile-title{font-size:25px}
.t3{left:607px;background:linear-gradient(180deg,#7a8566,#c86a6a 70%);padding-bottom:92px}
.t3 .tile-title{font-size:52px}
.t3 .tile-by{font-weight:700;text-transform:uppercase;font-size:13px}
.t4{left:903px;background:linear-gradient(90deg,#2a2a2a,#6a6a6a)}

/* headings */
.section-title{position:absolute;left:0;width:1200px;text-align:center;font-family:"Montserrat",sans-serif;font-weight:800;font-size:43px;letter-spacing:-1px}
.section-title em{font-style:normal;color:var(--teal)}

/* video cards */
.video-card{position:absolute;width:306px;height:294px;background:#fff;border-radius:8px;box-shadow:0 4px 18px rgba(0,0,0,.12);padding:6px}
.video-thumb{position:relative;height:224px;border-radius:4px}
.play{position:absolute;left:50%;top:50%;width:42px;height:30px;margin:-15px 0 0 -21px;background:#e8140c;border-radius:8px}
.play::after{content:"";position:absolute;left:16px;top:8px;border-left:12px solid #fff;border-top:7px solid transparent;border-bottom:7px solid transparent}
.video-caption{text-align:center;font-weight:700;font-size:17px;margin-top:24px}
.video-card.featured{background:var(--teal)}
.video-card.featured .video-caption{color:#fff;text-transform:uppercase}
.c1{left:113px}.c2{left:447px}.c3{left:781px}
.r1{top:1278px}.r2{top:1616px}

/* disciple */
.disciple{position:absolute;left:0;top:2017px;width:1200px;height:465px;background:var(--teal-wash)}
.study{position:absolute;top:146px;display:flex;gap:24px}
.study-photo{width:214px;height:214px;border-radius:50%}
.study h3{font-size:20px;font-weight:700;margin:20px 0 12px}
.study p{width:228px;font-size:14px;line-height:24px;color:var(--body);text-align:justify}
.link{display:inline-flex;gap:6px;align-items:center;margin-top:14px;color:var(--teal);font-weight:700;font-size:14px;text-decoration:underline;text-transform:uppercase}

/* about */
.about{position:absolute;left:0;top:2482px;width:1200px;height:488px;background:linear-gradient(90deg,#1fb6a0,#2bbba5 60%,#22b29c)}
.about-visual{position:absolute;left:40px;top:84px;width:512px;height:280px;border-radius:6px;background:linear-gradient(135deg,#7b8f7e,#3d5a52)}
.about h2{position:absolute;left:627px;top:62px;font-family:"Montserrat",sans-serif;font-weight:800;font-size:43px;color:#fff}
.about p{position:absolute;left:627px;width:462px;font-size:14px;line-height:27px;color:#fff}
.about .btn-pill{position:absolute;left:627px;top:363px;width:182px;height:52px;background:#fff;color:var(--teal);font-size:14px}

/* blog */
.blog-card{position:absolute;top:3128px;width:309px;height:409px;background:#fff;box-shadow:0 4px 18px rgba(0,0,0,.1)}
.blog-img{height:212px}
.blog-date{position:absolute;left:20px;top:197px;height:30px;padding:0 18px;background:var(--teal);color:#fff;font-size:13px;display:flex;align-items:center;gap:6px}
.blog-body{padding:40px 21px 0}
.blog-body h3{font-size:16px;line-height:23px;font-weight:700}
.blog-body p{font-size:14px;line-height:22px;color:var(--body);margin-top:12px}
.blog-body .link{text-decoration:none;margin-top:10px}

/* footer */
.site-footer{position:absolute;left:0;top:3628px;width:1200px;height:363px;background:var(--footer);color:#fff}
.site-footer h4{position:absolute;top:76px;font-size:18px;font-weight:700}
.contact-list{position:absolute;left:110px;top:116px;list-style:none;font-size:14px;line-height:20px}
.contact-list li{display:flex;gap:18px;margin-bottom:16px;width:270px}
.contact-list svg{flex:none;margin-top:3px}
.links{position:absolute;top:115px;list-style:none;font-size:14px;line-height:27px}
.subscribe{position:absolute;left:714px;top:113px;width:233px;height:44px;border-radius:22px;background:#fff;color:#888;font-size:12px;padding:14px 22px}
.btn-submit{position:absolute;left:965px;top:113px;width:123px;height:42px;border-radius:21px;background:var(--teal);font-weight:700;font-size:16px;display:flex;align-items:center;justify-content:center}
.consent{position:absolute;left:712px;top:183px;font-size:13px;font-weight:500}
.social{position:absolute;left:711px;top:222px;display:flex;gap:10px}
.social span{width:32px;height:32px;border:1.5px solid #fff;border-radius:50%}
.copyright{position:absolute;left:0;top:320px;width:1200px;text-align:center;font-size:13px}
</style>
</head>
<body>

<header class="site-header">
  <a class="brand" href="#"><span class="brand-mark"></span><span class="brand-name">KINDRED PATH</span></a>
  <nav class="main-nav"><a class="active" href="#">Home</a><a href="#">Bible Studies</a><a href="#">Video Series</a></nav>
  <a class="btn-access" href="#">GET ACCESS</a>
</header>

<section class="hero" role="img" aria-label="Photo of a teacher holding a Bible beside a river">
  <h1 class="hero-title">THE LAMP SERIES</h1>
  <p class="hero-text">Lorem ipsum dolor sit amet, consectetur adipiscing elit, sed do tempor incididunt ut labore et aliqua.</p>
  <a class="btn-pill" href="#">Watch Now
    <svg width="15" height="15" viewBox="0 0 16 16"><circle cx="8" cy="8" r="8" fill="#fff"/><path d="M6 4l4 4-4 4" stroke="#00bba5" stroke-width="2" fill="none"/></svg></a>
  <div class="dots"><span></span><span></span><span></span></div>
</section>

<div class="tile t1" role="img" aria-label="Series cover: woman smiling in a garden"><span class="tile-title">Every<br>Season</span>With Maren Ellis</div>
<div class="tile t2" role="img" aria-label="Series cover: speaker silhouette in teal"><span class="tile-title">Made With Purpose</span>
  <svg width="56" height="20" viewBox="0 0 56 20"><path d="M2 10h50M44 3l8 7-8 7" stroke="#fff" stroke-width="2.5" fill="none"/></svg></div>
<div class="tile t3" role="img" aria-label="Series cover: teacher in pink shirt at a covered bridge"><span class="tile-title">KINDLE</span><span class="tile-by">With Walt Brenner</span></div>
<div class="tile t4" role="img" aria-label="Series cover: man in glasses in profile"><span class="tile-title">QUIET<br>DAWN</span>With Silas Ward</div>

<h2 class="section-title" style="top:1190px">VIDEO <em>SERIES</em></h2>

<article class="video-card c1 r1"><div class="video-thumb" role="img" aria-label="Speaker reading from a Bible" style="background:linear-gradient(180deg,#8a6a4a,#2e2a28)"><span class="play"></span></div><p class="video-caption">Lorem ipsum dolor sit amet</p></article>
<article class="video-card c2 r1"><div class="video-thumb" role="img" aria-label="Speaker with a city skyline" style="background:linear-gradient(180deg,#c9cdd2,#8c8a8a)"><span class="play"></span></div><p class="video-caption">Lorem ipsum dolor sit amet</p></article>
<article class="video-card c3 r1"><div class="video-thumb" role="img" aria-label="Young man holding a Bible" style="background:linear-gradient(135deg,#d7c7b3,#5a6b86)"><span class="play"></span></div><p class="video-caption">Lorem ipsum dolor sit amet</p></article>
<article class="video-card c1 r2"><div class="video-thumb" role="img" aria-label="Teacher at a covered bridge" style="background:linear-gradient(180deg,#6f7d5e,#c96f6f)"><span class="play"></span></div><p class="video-caption">Lorem ipsum dolor sit amet</p></article>
<article class="video-card c2 r2 featured"><div class="video-thumb" role="img" aria-label="Speaker in a studio" style="background:linear-gradient(180deg,#3e4446,#b9aa96)"><span class="play"></span></div><p class="video-caption">Download Now
  <svg width="14" height="14" viewBox="0 0 16 16" style="vertical-align:-2px;margin-left:4px"><circle cx="8" cy="8" r="8" fill="#fff"/><path d="M6 4l4 4-4 4" stroke="#00bba5" stroke-width="2" fill="none"/></svg></p></article>
<article class="video-card c3 r2"><div class="video-thumb" role="img" aria-label="Teacher in a church hall" style="background:linear-gradient(180deg,#b9b2a8,#8a4f54)"><span class="play"></span></div><p class="video-caption">Lorem ipsum dolor sit amet</p></article>

<section class="disciple">
  <h2 class="section-title" style="top:58px">DISCIPLE <em>EVERYONE</em></h2>
  <div class="study" style="left:111px">
    <div class="study-photo" role="img" aria-label="Hands resting on an open Bible" style="background:linear-gradient(135deg,#c9c1b8,#6a5e58)"></div>
    <div><h3>Topical Studies</h3><p>Lorem ipsum dolor sit consectetur adipiscing elit, sed do eiusmod tempor incididunt ut labore et dolore magna aliqua.</p>
    <a class="link" href="#">Learn More
      <svg width="13" height="13" viewBox="0 0 16 16"><circle cx="8" cy="8" r="8" fill="#00bba5"/><path d="M6 4l4 4-4 4" stroke="#fff" stroke-width="2" fill="none"/></svg></a></div>
  </div>
  <div class="study" style="left:622px">
    <div class="study-photo" role="img" aria-label="Woman holding a Bible at sunset" style="background:radial-gradient(circle at 30% 40%,#f5c46a,#7a6a4c 70%)"></div>
    <div><h3>Doctrinal Studies</h3><p>Lorem ipsum dolor sit consectetur adipiscing elit, sed do eiusmod tempor incididunt ut labore et dolore magna aliqua.</p>
    <a class="link" href="#">Learn More
      <svg width="13" height="13" viewBox="0 0 16 16"><circle cx="8" cy="8" r="8" fill="#00bba5"/><path d="M6 4l4 4-4 4" stroke="#fff" stroke-width="2" fill="none"/></svg></a></div>
  </div>
</section>

<section class="about">
  <div class="about-visual" role="img" aria-label="Photo of a speaker teaching outdoors"></div>
  <h2>ABOUT US</h2>
  <p style="top:132px">Lorem ipsum dolor sit amet, consectetur adipiscing elit, sed do eiusmod tempor incididunt ut labore et dolore magna aliqua. Ut enim ad minim veniam, quis nostrud exercitation ullamco laboris nisi ut aliquip ex ea commodo consequat.</p>
  <p style="top:253px">Duis aute irure dolor in reprehenderit in voluptate velit esse cillum dolore eu fugiat nulla pariatur. Excepteur sint occaecat cupidatat non proident, sunt in culpa qui officia deserunt mollit anim id est laborum.</p>
  <a class="btn-pill" href="#">Read More
    <svg width="14" height="14" viewBox="0 0 16 16"><circle cx="8" cy="8" r="8" fill="#00bba5"/><path d="M6 4l4 4-4 4" stroke="#fff" stroke-width="2" fill="none"/></svg></a>
</section>

<h2 class="section-title" style="top:3045px">LATEST BLOG</h2>

<article class="blog-card" style="left:111px"><div class="blog-img" role="img" aria-label="Hand turning the pages of a Bible" style="background:linear-gradient(135deg,#3d4a4e,#c9a57a)"></div><span class="blog-date">▦ Jan 2, 2022</span>
  <div class="blog-body"><h3>Lorem ipsum amet, consectetur adipiscing elit</h3><p>Sed ut perspiciatis unde omnis iste natus sit voluptatem accusantium</p><a class="link" href="#">Read More
    <svg width="13" height="13" viewBox="0 0 16 16"><circle cx="8" cy="8" r="8" fill="#00bba5"/><path d="M6 4l4 4-4 4" stroke="#fff" stroke-width="2" fill="none"/></svg></a></div></article>
<article class="blog-card" style="left:445px"><div class="blog-img" role="img" aria-label="Woman reading under a tree" style="background:linear-gradient(180deg,#9cc48e,#4b6ea0)"></div><span class="blog-date">▦ Jan 2, 2022</span>
  <div class="blog-body"><h3>Lorem ipsum amet, consectetur adipiscing elit</h3><p>Sed ut perspiciatis unde omnis iste natus sit voluptatem accusantium</p><a class="link" href="#">Read More
    <svg width="13" height="13" viewBox="0 0 16 16"><circle cx="8" cy="8" r="8" fill="#00bba5"/><path d="M6 4l4 4-4 4" stroke="#fff" stroke-width="2" fill="none"/></svg></a></div></article>
<article class="blog-card" style="left:778px"><div class="blog-img" role="img" aria-label="Group of friends in a Bible study" style="background:linear-gradient(135deg,#8c7c74,#3a3642)"></div><span class="blog-date">▦ Jan 2, 2022</span>
  <div class="blog-body"><h3>Lorem ipsum amet, consectetur adipiscing elit</h3><p>Sed ut perspiciatis unde omnis iste natus sit voluptatem accusantium</p><a class="link" href="#">Read More
    <svg width="13" height="13" viewBox="0 0 16 16"><circle cx="8" cy="8" r="8" fill="#00bba5"/><path d="M6 4l4 4-4 4" stroke="#fff" stroke-width="2" fill="none"/></svg></a></div></article>

<footer class="site-footer">
  <h4 style="left:110px">Contact Us</h4>
  <ul class="contact-list">
    <li><svg width="12" height="14" viewBox="0 0 12 16"><path d="M6 0a6 6 0 0 0-6 6c0 4.5 6 10 6 10s6-5.5 6-10a6 6 0 0 0-6-6zm0 8.5a2.5 2.5 0 1 1 0-5 2.5 2.5 0 0 1 0 5z" fill="#00bba5"/></svg>Lorem ipsum dolor sit consectetur adipiscing elit</li>
    <li><svg width="14" height="11" viewBox="0 0 14 11"><rect width="14" height="11" rx="1" fill="#00bba5"/><path d="M1 1l6 5 6-5" stroke="#232323" fill="none"/></svg>info@kindredpath.org</li>
    <li><svg width="13" height="13" viewBox="0 0 16 16"><path d="M3 1l3 3-2 2c1 2 3 4 6 6l2-2 3 3-2 2C7 15 1 9 1 3z" fill="#00bba5"/></svg>+1 888-888-8888</li>
    <li><svg width="13" height="13" viewBox="0 0 14 14"><rect width="14" height="14" rx="1" fill="#00bba5"/><rect x="3" y="3" width="8" height="4" fill="#232323"/></svg>+1 (123) 456 - 7890</li>
  </ul>
  <h4 style="left:423px">Links</h4>
  <ul class="links" style="left:423px"><li>Home</li><li>Bible Studies</li><li>Video Series</li><li>Services</li><li>Blog</li></ul>
  <ul class="links" style="left:535px"><li>Terms &amp; Condition</li><li>Privacy Policy</li><li>Support</li><li>Site Map</li><li>Contact Us</li></ul>
  <h4 style="left:710px">Subscribe for Updates</h4>
  <div class="subscribe">Emaill Address</div>
  <a class="btn-submit" href="#">SUBMIT</a>
  <p class="consent">☑&nbsp; Yes, Please Contact me.</p>
  <div class="social" aria-label="Social links"><span></span><span></span><span></span></div>
  <p class="copyright">© 2022 Kindred Path &nbsp;| &nbsp;All Rights Reserved</p>
</footer>

</body>
</html>
```